Financial Services Flyer in English one side Spanish the other side

Hello - we are looking for good flyer that will be one side English, the other side exact same language in Spanish.... For the Flyer -

We show businesses how to save Thousands by Eliminating the percentage you are paying to accept Credit & Debit Cards... No more %!?? Yes, it's true!

We provide a free placed terminal or POS with a minimal monthly service fee.

On the Spanish Side; include "We specialize in Latina Businesses with Spanish Sales and Support staff"
We specialize in Latina Businesses with Spanish Sales and Support staff.
Nos especializamos en negocios latinos con personal de ventas y soporte en espaƱol.

Target Market(s)

Any business

Industry/Entity Type

any business that accepts credit cards.

Requirements
Must have
• WE need a white box on the flyers to place a label with the various agents name and contact.
Nice to have
• You can include pictures I uploaded, especially the logo and some equipment...

```html
<!DOCTYPE html>
<html lang="en">
<head>
<meta charset="utf-8">
<title>Lumora Payments Flyers – English / Español</title>
<link href="https://fonts.googleapis.com/css2?family=Poppins:wght@400;600;700&display=swap" rel="stylesheet">
<style>
  :root {
    --board: #a8a8a8;
    --brand-blue: #0f5aa8;
    --brand-yellow: #e4b51a;
    --paper: #ffffff;
    --photo-warm: #e9d2bd;
    --photo-cool: #dfe6dd;
    --photo-money: #c9d3bd;
    --photo-gold: #d9b766;
    --device: #3b3f47;
  }
  * { margin: 0; padding: 0; box-sizing: border-box; }
  html, body { width: 1200px; height: 846px; overflow: hidden; }
  body { background: var(--board); position: relative; font-family: 'Poppins', sans-serif; }
  .flyer { position: absolute; top: 45px; width: 535px; height: 756px; background: var(--paper); overflow: hidden; }
  .flyer--english { left: 42px; }
  .flyer--spanish { left: 623px; }
  .flyer svg { display: block; width: 100%; height: 100%; }
  .brand-name { font-family: 'Poppins', sans-serif; font-weight: 700; font-size: 66px; fill: var(--brand-blue); }
  .intro { font-family: 'Poppins', sans-serif; font-size: 25px; fill: var(--brand-yellow); }
  .headline { font-family: 'Poppins', sans-serif; font-weight: 700; font-size: 39px; fill: var(--paper); }
  .offer { font-family: 'Poppins', sans-serif; font-size: 27px; fill: var(--paper); }
  .cta { font-family: 'Poppins', sans-serif; font-size: 20px; letter-spacing: 1.5px; fill: var(--paper); }
  .outline { fill: none; stroke: var(--brand-yellow); stroke-width: 3; }
  .outline-light { fill: none; stroke: var(--paper); stroke-width: 2; }
  .arrow { fill: var(--brand-yellow); }
</style>
</head>
<body>

<!-- English side -->
<section class="flyer flyer--english" aria-label="English flyer">
  <svg viewBox="0 0 1023 1446" xmlns="http://www.w3.org/2000/svg">
    <defs>
      <radialGradient id="warmTone" cx="50%" cy="45%" r="60%">
        <stop offset="0%" stop-color="#d9a07a"/>
        <stop offset="60%" stop-color="#b8743f"/>
        <stop offset="100%" stop-color="#f3ebe4"/>
      </radialGradient>
    </defs>

    <text class="brand-name" x="30" y="100">Lumora</text>

    <rect x="405" y="40" width="200" height="215" fill="#eef3f9" role="img" aria-label="Decorative dot grid"/>

    <rect x="10" y="175" width="390" height="230" rx="14" fill="var(--photo-money)" role="img" aria-label="Photo of a hand holding cash beside a card payment terminal"/>

    <path d="M0 420 C160 380 360 385 470 440 L1023 440 L1023 1446 L0 1446 Z" fill="var(--brand-blue)"/>

    <circle cx="800" cy="330" r="372" fill="var(--brand-yellow)"/>
    <circle cx="815" cy="318" r="350" fill="url(#warmTone)" role="img" aria-label="Photo of a smiling shopper holding payment cards and a shopping bag"/>

    <polyline class="outline" points="0,430 105,535 0,640"/>
    <polyline class="outline" points="0,470 65,535 0,600"/>
    <polyline class="outline" points="0,510 25,535 0,560"/>

    <g class="arrow">
      <polygon points="150,518 178,534 150,550"/>
      <polygon points="190,518 218,534 190,550"/>
      <polygon points="230,518 258,534 230,550"/>
      <polygon points="270,518 298,534 270,550"/>
      <polygon points="310,518 338,534 310,550"/>
      <polygon points="905,83 923,94 905,105"/>
      <polygon points="933,83 951,94 933,105"/>
      <polygon points="961,83 979,94 961,105"/>
      <polygon points="989,83 1007,94 989,105"/>
      <polygon points="1015,83 1023,88 1023,100 1015,105"/>
    </g>

    <text class="intro">
      <tspan x="33" y="656">Lumora Payments take the PAIN out of</tspan>
      <tspan x="33" y="692">Payment Processing by delivering more</tspan>
      <tspan x="33" y="728">of your profit to you!</tspan>
    </text>

    <text class="headline">
      <tspan x="33" y="802">We show businesses how to save Thousands</tspan>
      <tspan x="33" y="864">by Eliminating the percentage you are</tspan>
      <tspan x="33" y="926">paying to accept Credit &amp; Debit Cards Pay</tspan>
      <tspan x="33" y="988">ZERO % with Lumora!</tspan>
    </text>

    <path d="M0 1095 C220 1050 470 1140 585 1446 L0 1446 Z" fill="var(--brand-yellow)"/>

    <g transform="rotate(25 160 1085)">
      <rect class="outline-light" x="125" y="1050" width="70" height="70"/>
      <rect class="outline-light" x="138" y="1063" width="44" height="44"/>
      <rect class="outline-light" x="150" y="1075" width="20" height="20"/>
    </g>

    <text class="offer">
      <tspan x="36" y="1192">We provide a free</tspan>
      <tspan x="36" y="1250">placed terminal or POS</tspan>
      <tspan x="36" y="1307">with a minimal monthly</tspan>
      <tspan x="36" y="1365">service fee.</tspan>
    </text>

    <rect x="435" y="1160" width="75" height="185" rx="10" fill="var(--device)" role="img" aria-label="Photo of a countertop card terminal"/>

    <rect x="600" y="1000" width="386" height="334" fill="none" stroke="var(--brand-yellow)" stroke-width="3"/>
    <rect x="609" y="1009" width="368" height="316" fill="var(--paper)"/>

    <text class="cta" text-anchor="middle">
      <tspan x="793" y="1382">Contact Our Partner Today and</tspan>
      <tspan x="793" y="1412">Activate Your Savings</tspan>
    </text>
  </svg>
</section>

<!-- Spanish side -->
<section class="flyer flyer--spanish" aria-label="Folleto en español" lang="es">
  <svg viewBox="0 0 1023 1446" xmlns="http://www.w3.org/2000/svg">
    <defs>
      <linearGradient id="portraitTone" x1="0" y1="0" x2="1" y2="1">
        <stop offset="0%" stop-color="#f7f1ec"/>
        <stop offset="55%" stop-color="#e2b89a"/>
        <stop offset="100%" stop-color="#2b2324"/>
      </linearGradient>
      <linearGradient id="moneyTone" x1="0" y1="0" x2="1" y2="1">
        <stop offset="0%" stop-color="var(--photo-gold)"/>
        <stop offset="100%" stop-color="#cfd5c4"/>
      </linearGradient>
    </defs>

    <text class="brand-name" x="30" y="100">Lumora</text>

    <rect x="405" y="45" width="200" height="215" fill="#eef3f9" role="img" aria-label="Patrón decorativo de puntos"/>

    <circle cx="840" cy="640" r="540" fill="var(--brand-yellow)"/>
    <circle cx="860" cy="650" r="518" fill="var(--paper)"/>
    <rect x="345" y="100" width="678" height="580" fill="url(#portraitTone)" opacity="0.9" role="img" aria-label="Foto de una mujer sonriente con billetes y una tarjeta"/>

    <g class="arrow">
      <polygon points="498,285 470,300 498,315"/>
      <polygon points="536,285 508,300 536,315"/>
      <polygon points="574,285 546,300 574,315"/>
      <polygon points="612,285 584,300 612,315"/>
      <polygon points="650,285 622,300 650,315"/>
    </g>

    <rect x="55" y="415" width="205" height="262" rx="16" fill="var(--device)" role="img" aria-label="Foto de una terminal de pago portátil"/>

    <path d="M0 800 C100 730 200 690 320 668 L1023 668 L1023 1446 L0 1446 Z" fill="var(--brand-blue)"/>

    <g transform="rotate(45 35 790)">
      <rect class="outline" x="-35" y="720" width="140" height="140"/>
      <rect class="outline" x="-10" y="745" width="90" height="90"/>
      <rect x="15" y="770" width="40" height="40" fill="var(--paper)" stroke="var(--brand-yellow)" stroke-width="3"/>
    </g>

    <text class="headline" text-anchor="end">
      <tspan x="990" y="782">Nos especializamos en negocios</tspan>
      <tspan x="990" y="844">latinos con personal de ventas</tspan>
      <tspan x="990" y="906">y soporte en español</tspan>
    </text>

    <g class="arrow">
      <polygon points="182,940 225,966 182,992"/>
      <polygon points="247,940 290,966 247,992"/>
      <polygon points="312,940 355,966 312,992"/>
      <polygon points="377,940 420,966 377,992"/>
      <polygon points="442,940 485,966 442,992"/>
    </g>

    <path d="M0 1062 C260 1030 500 1170 590 1446 L0 1446 Z" fill="var(--brand-yellow)"/>
    <path d="M0 1088 C250 1062 480 1200 568 1446 L0 1446 Z" fill="url(#moneyTone)" role="img" aria-label="Foto de llaves doradas sobre billetes"/>

    <rect x="600" y="1000" width="386" height="334" fill="none" stroke="var(--brand-yellow)" stroke-width="3"/>
    <rect x="609" y="1009" width="368" height="316" fill="var(--paper)"/>

    <text class="cta" text-anchor="middle">
      <tspan x="793" y="1382">Contacte a nuestro socio hoy</tspan>
      <tspan x="793" y="1412">y active sus ahorros</tspan>
    </text>
  </svg>
</section>

</body>
</html>
```